Start up International Security Business Needs a Web Design

Based in Edinburgh UK, Morvane Global Services (www.morvanegs.example) provides security services of various types in challenging or high threat environments internationally for government and private sector organizations. We provide risk assessments, security audits and training, medical support, close protection for individuals, groups and events, crisis management, and evacuation coordination; we enable businesses to operate in challenging locations. Our experts are highly trained and qualified with exceptional experience worldwide.
The name Morvane was selected in competition and derives from Greek Mythology where it was a giant man of bronze gifted by Zeus to protect Europa from invaders and pirates, circling the island of Crete three times daily (essentially establishing a protective perimeter). The centre of the current logo (inside the "O") is a stylized symbol of Zeus; we use it as a customized "bullet" on documents and acts as an abbreviated logo.
We purposefully omitted any reference to security in the name/logo and the web-page should be discreet in the same manner - we provide services of this nature but do not draw attention to ourselves. Generic images for visuals should be used as opposed to any existing stock photography we possess as a company. Imagery that relay protection, an international reach, innovation, modern vistas, varied countrysides (desert, jungle, urban settings, an old fortress?) would be seen positively.
The current colour of blue and white in the principal logo has received positive response for the clean lines, and the grey-ish scale writing similarly works. The "O" with the symbol inside has been used as customized "bullets" inside of documents, and we envisioned several other potential uses for web pages, etc.
However the integration of bronze as a third colour given the origin of Morvane could be a consideration as well.
The final design should communicate clarity, an international reach in difficult areas with our broad experience and strength without being aggressive. There must be a section where the countries we have experience operating in is displayed graphically (i.e. a global map where the countries are coloured in). Countries are USA, Canada, UK, France, Bosnia, UAE, Qatar, Libya, Tunisia, Afghanistan, Iraq, Turkey, Sudan, Egypt, Central African Republic, Somalia, Rwanda, Somaliland. Additional sections should include "Our Clients", "Our Services", "Our Expertise", "Join Our Team" which should have a personal details form and ability to upload a CV, "Our Contact Details" which should also allow for submission of a web enquiry
Reason: Extension granted at the request of several designers in order to conceptualize solutions whilst initial selection process begins. Feedback on each design submitted will be provided. Very many thanks to all who took the time to share their vision for our company's website.
Morvane GS
Target Market(s)
Private Sector energy, logistics, and infrastructure companies along with government organizations
Industry/Entity Type
Security
Logo Text
Morvane
Number of Pages Required
3 page
Requirements
Must have
- There must be a section where the countries we have experience operating in is displayed graphically (i.e. a global map where the countries are coloured in). Countries are USA, Canada, UK, France, Bosnia, UAE, Qatar, Libya, Tunisia, Afghanistan, Iraq, Turkey, Sudan, Egypt, Central African Republic, Somalia, Rwanda, Somaliland. Additional sections should include "Our Clients", "Our Services", "Our Expertise", "Join Our Team" which should have a personal details form and ability to upload a CV, "Our Contact Details" which should also allow for submission of a web enquiry
Should not have
- Aggressive pictures of guards, weapons, etc

```html
<!DOCTYPE html>
<html lang="en">
<head>
<meta charset="utf-8">
<title>Morvane Global Services</title>
<link href="https://fonts.googleapis.com/css2?family=Roboto:wght@300;400;500;700&family=Roboto+Condensed:wght@700&display=swap" rel="stylesheet">
<style>
:root{
  --blue:#1d86c8;
  --blue-dark:#13639a;
  --orange:#f5931f;
  --ink:#333;
  --muted:#777;
  --soft:#f1f2f3;
  --footer:#3b3c3e;
  --footer-dark:#2e2f31;
  --white:#fff;
}
*{box-sizing:border-box;margin:0;padding:0}
html,body{width:711px;height:1200px;overflow:hidden;background:var(--white)}
body{font-family:"Roboto",Arial,sans-serif;color:var(--ink);font-size:7px;line-height:1.45}
.page{position:relative;width:711px;height:1200px;overflow:hidden}

/* header */
.site-header{height:52px;position:relative;border-bottom:1px solid #e3e3e3}
.brand{position:absolute;left:22px;top:6px}
.brand-name{font-family:"Roboto Condensed",Arial,sans-serif;font-size:30px;font-weight:700;color:var(--blue);line-height:1}
.brand-tag{font-size:6px;color:var(--blue);letter-spacing:.6px;text-transform:uppercase}
.main-nav{position:absolute;left:222px;top:24px;display:flex;gap:4px}
.main-nav a{font-size:7px;color:#555;text-decoration:none;padding:4px 7px;border:1px solid transparent}
.main-nav a.active{background:var(--blue);color:var(--white)}
.join-btn{position:absolute;left:447px;top:0;background:var(--orange);color:var(--white);font-size:6.5px;padding:3px 9px}
.follow{position:absolute;left:512px;top:2px;display:flex;align-items:center;gap:3px;font-size:6.5px;color:var(--orange)}
.follow i{display:block;width:9px;height:9px;border-radius:50%;background:var(--blue)}
.phone{position:absolute;left:542px;top:18px;color:var(--blue);font-size:13px;font-weight:500;display:flex;align-items:center;gap:4px}
.phone small{display:block;font-size:6px;color:#888;font-weight:400}

/* hero */
.hero{position:relative;height:258px;background:linear-gradient(180deg,#b8c6d3 0%,#8596a8 45%,#4d5a67 100%)}
.hero-caption{position:absolute;left:0;right:0;bottom:0;height:56px;background:rgba(20,40,60,.55);color:var(--white);text-align:center;font-size:10px;line-height:1.35;padding-top:8px}

/* welcome */
.welcome{text-align:center;padding:18px 60px 0;height:120px}
.section-title{font-size:13px;font-weight:400;color:var(--ink);text-align:center}
.section-title b{color:var(--blue);font-weight:500}
.welcome .section-title{color:var(--blue)}
.welcome p{margin-top:6px;color:var(--muted);font-size:6.5px}
.read-more{display:inline-block;margin-top:4px;color:var(--blue);font-size:6.5px}

/* services */
.services{background:var(--soft);height:212px;padding-top:16px}
.services .section-title b{color:var(--blue)}
.services-intro{text-align:center;font-size:6px;color:var(--muted);margin-top:3px}
.service-grid{display:flex;justify-content:center;gap:14px;margin-top:14px}
.service{width:80px;text-align:center}
.service-icon{width:52px;height:52px;margin:0 auto;border-radius:50%;background:var(--blue);border:3px solid #cfe3f1;display:flex;align-items:center;justify-content:center}
.service-icon.bronze{background:var(--orange);border-color:#fbdcb6}
.service h3{font-size:6.5px;font-weight:500;margin-top:8px;color:var(--ink)}
.service p{font-size:5.5px;color:var(--muted);margin-top:3px}

/* why */
.why{height:196px;position:relative;padding:20px 0 0 22px}
.why .section-title{text-align:left;font-size:14px}
.why .section-title b{color:var(--blue)}
.why-rule{width:40px;height:2px;background:var(--blue);margin:4px 0 8px}
.why-text{width:330px;color:var(--muted);font-size:6.3px}
.why-list{list-style:none;margin-top:6px;width:330px}
.why-list li{display:flex;gap:5px;align-items:center;color:var(--muted);font-size:6.3px;margin-bottom:5px}
.why-video{position:absolute;left:395px;top:12px;width:250px;height:150px;background:linear-gradient(135deg,#c9ccd0,#6c7075 60%,#2a2c2f);border-radius:3px}
.why-video-label{position:absolute;left:395px;top:166px;width:250px;text-align:center;font-size:7px;color:var(--ink)}

/* clients */
.clients{height:118px;padding-top:14px;border-top:1px solid #eee}
.clients .section-title{font-size:14px}
.clients .section-title b{color:var(--blue)}
.client-row{display:flex;justify-content:center;align-items:center;gap:22px;margin-top:20px}
.client{font-size:14px;font-weight:700;color:#555;display:flex;align-items:center;gap:4px}
.client i{display:block;width:10px;height:10px;background:#bbb}

/* footer */
.site-footer{height:230px;background:var(--footer);color:#ccc;position:relative}
.footer-col{position:absolute;top:14px}
.contact-col{left:22px;width:160px}
.footer-head{font-size:8px;color:var(--white);font-weight:500;padding-bottom:5px;border-bottom:1px solid #555;margin-bottom:8px}
.contact-item{display:flex;gap:6px;margin-bottom:9px;font-size:6px;line-height:1.4}
.contact-item svg{flex:none}
.map-col{left:196px;width:280px;text-align:center}
.map{margin-top:6px;height:150px;border-radius:2px;background:linear-gradient(180deg,#5b5e62,#4a4d51);position:relative}
.country-list{position:absolute;left:50px;top:22px;width:180px;height:110px;background:rgba(40,40,42,.92);display:grid;grid-template-columns:repeat(3,1fr);padding:8px 10px;gap:1px 6px;text-align:left;font-size:6px;color:#ddd}
.country-list span::before{content:"";display:inline-block;width:3px;height:3px;background:var(--orange);margin-right:3px;vertical-align:middle}
.inquiry-col{left:495px;width:195px;background:var(--footer-dark);padding:8px;top:10px;height:200px}
.inquiry-col .footer-head{border:0;font-size:9px}
.field{height:16px;background:var(--white);margin-bottom:6px;font-size:6px;color:#999;padding:4px 5px}
.field.msg{height:50px}
.submit{display:inline-block;background:var(--orange);color:var(--white);font-size:6.5px;font-weight:500;padding:4px 12px}
.copyright{position:absolute;left:0;right:0;bottom:0;height:20px;background:var(--orange);color:var(--white);font-size:6px;text-align:center;line-height:20px}
</style>
</head>
<body>
<div class="page">

<header class="site-header">
  <div class="brand">
    <div class="brand-name">Morvane</div>
    <div class="brand-tag">Global Services</div>
  </div>
  <nav class="main-nav">
    <a class="active">Home</a><a>About Us</a><a>Services</a><a>Our Expertise</a><a>Clients</a><a>Contact Us</a>
  </nav>
  <div class="join-btn">Join Our Team</div>
  <div class="follow">Follow us on <i></i><i></i><i></i><i></i></div>
  <div class="phone">
    <svg width="12" height="12" viewBox="0 0 24 24"><path fill="#1d86c8" d="M6.6 10.8a15 15 0 006.6 6.6l2.2-2.2c.3-.3.7-.4 1-.2 1.1.4 2.3.6 3.6.6.6 0 1 .4 1 1V20c0 .6-.4 1-1 1A17 17 0 013 4c0-.6.4-1 1-1h3.5c.6 0 1 .4 1 1 0 1.3.2 2.5.6 3.6.1.3 0 .7-.2 1z"/></svg>
    <div><small>Call Us Today</small>555-014-2290</div>
  </div>
</header>

<section class="hero" role="img" aria-label="Photograph of a modern city skyline of high-rise towers">
  <div class="hero-caption">We Provide Security Services of Various Types In Challenging or High Threat Environments<br>Internationally For Government And Private Sector Organizations.</div>
</section>

<section class="welcome">
  <h2 class="section-title">Welcome to <b>Morvane</b> Global Services</h2>
  <p>Our team supports organisations working in demanding regions with calm, careful planning and steady local knowledge. We assess each setting, prepare people for the risks they may meet and stay close while the work is carried out, so that projects can move forward with confidence and without drawing attention.</p>
  <p>Clients in energy, logistics and infrastructure rely on our advisers for clear guidance, trained staff and dependable support from first survey to safe return.</p>
  <span class="read-more">Read more</span>
</section>

<section class="services">
  <h2 class="section-title"><b>Services</b> We Provide</h2>
  <p class="services-intro">Practical support for people and projects operating in difficult places around the world.</p>
  <div class="service-grid">
    <div class="service"><div class="service-icon bronze"><svg width="22" height="22" viewBox="0 0 24 24" fill="none" stroke="#fff" stroke-width="2"><circle cx="12" cy="12" r="8"/><path d="M12 7v5l3 3"/></svg></div><h3>Risk Assessments</h3><p>Clear review of threats before any work begins.</p></div>
    <div class="service"><div class="service-icon"><svg width="22" height="22" viewBox="0 0 24 24" fill="none" stroke="#fff" stroke-width="2"><path d="M5 12l4 4 10-10"/></svg></div><h3>Security Audits And Training</h3><p>Site checks and courses for staff.</p></div>
    <div class="service"><div class="service-icon"><svg width="22" height="22" viewBox="0 0 24 24" fill="none" stroke="#fff" stroke-width="3"><path d="M12 5v14M5 12h14"/></svg></div><h3>Medical Support</h3><p>Trained medics ready on every task.</p></div>
    <div class="service"><div class="service-icon"><svg width="22" height="22" viewBox="0 0 24 24" fill="none" stroke="#fff" stroke-width="2"><path d="M12 3l7 3v6c0 4-3 7-7 9-4-2-7-5-7-9V6z"/></svg></div><h3>Protection For Individuals</h3><p>Discreet cover for people and events.</p></div>
    <div class="service"><div class="service-icon"><svg width="22" height="22" viewBox="0 0 24 24" fill="none" stroke="#fff" stroke-width="2"><path d="M4 10h4l7-5v14l-7-5H4z"/></svg></div><h3>Crisis Management</h3><p>Steady response when plans change.</p></div>
    <div class="service"><div class="service-icon"><svg width="22" height="22" viewBox="0 0 24 24" fill="none" stroke="#fff" stroke-width="2"><path d="M4 12h14M13 6l6 6-6 6"/></svg></div><h3>Evacuation Coordination</h3><p>Safe routes out for whole teams.</p></div>
  </div>
</section>

<section class="why">
  <h2 class="section-title"><b>Why</b> Choose Us</h2>
  <div class="why-rule"></div>
  <p class="why-text">Our advisers bring long field experience, quiet professionalism and a global network of trusted partners to every assignment we accept.</p>
  <ul class="why-list">
    <li><svg width="8" height="8" viewBox="0 0 24 24" fill="none" stroke="#1d86c8" stroke-width="3"><path d="M4 12l5 5 11-11"/></svg>Highly trained and qualified staff worldwide</li>
    <li><svg width="8" height="8" viewBox="0 0 24 24" fill="none" stroke="#1d86c8" stroke-width="3"><path d="M4 12l5 5 11-11"/></svg>Experience across desert, jungle and urban settings</li>
    <li><svg width="8" height="8" viewBox="0 0 24 24" fill="none" stroke="#1d86c8" stroke-width="3"><path d="M4 12l5 5 11-11"/></svg>Discreet support that keeps projects moving</li>
    <li><svg width="8" height="8" viewBox="0 0 24 24" fill="none" stroke="#1d86c8" stroke-width="3"><path d="M4 12l5 5 11-11"/></svg>Trusted by government and private sector clients</li>
    <li><svg width="8" height="8" viewBox="0 0 24 24" fill="none" stroke="#1d86c8" stroke-width="3"><path d="M4 12l5 5 11-11"/></svg>Planning and reporting that is clear and honest</li>
  </ul>
  <div class="why-video" role="img" aria-label="Hands holding a tablet showing a company video"></div>
  <div class="why-video-label">View Video</div>
</section>

<section class="clients">
  <h2 class="section-title">Our <b>Clients</b></h2>
  <div class="client-row">
    <span class="client"><i></i>Norlik</span>
    <span class="client">Vantor</span>
    <span class="client"><i></i>Kestrel</span>
    <span class="client">Brightmoor</span>
    <span class="client"><i></i>Norlik</span>
    <span class="client">Dalven</span>
  </div>
</section>

<footer class="site-footer">
  <div class="footer-col contact-col">
    <div class="footer-head">Contact Information</div>
    <div class="contact-item"><svg width="9" height="9" viewBox="0 0 24 24"><path fill="#f5931f" d="M12 2a7 7 0 00-7 7c0 5 7 13 7 13s7-8 7-13a7 7 0 00-7-7zm0 9.5A2.5 2.5 0 1112 6a2.5 2.5 0 010 5.5z"/></svg><span>Postal Address<br>Street Name, City Name, State, Country</span></div>
    <div class="contact-item"><svg width="9" height="9" viewBox="0 0 24 24"><path fill="#f5931f" d="M6.6 10.8a15 15 0 006.6 6.6l2.2-2.2c.3-.3.7-.4 1-.2 1.1.4 2.3.6 3.6.6.6 0 1 .4 1 1V20c0 .6-.4 1-1 1A17 17 0 013 4c0-.6.4-1 1-1h3.5c.6 0 1 .4 1 1 0 1.3.2 2.5.6 3.6.1.3 0 .7-.2 1z"/></svg><span>Telephone<br>555-014-2290</span></div>
    <div class="contact-item"><svg width="9" height="9" viewBox="0 0 24 24"><path fill="#f5931f" d="M3 5h18v14H3zm2 2v.5l7 5 7-5V7z"/></svg><span>Email<br>hello@morvanegs.example</span></div>
    <div class="contact-item"><svg width="9" height="9" viewBox="0 0 24 24"><circle cx="12" cy="12" r="9" fill="#f5931f"/></svg><span>Web<br>www.morvanegs.example</span></div>
  </div>
  <div class="footer-col map-col">
    <div class="footer-head" style="border:0;text-align:center">We Have Experience Operating In</div>
    <div class="map" role="img" aria-label="World map with the countries of operation coloured in">
      <div class="country-list">
        <span>USA</span><span>Canada</span><span>UK</span>
        <span>France</span><span>Bosnia</span><span>UAE</span>
        <span>Qatar</span><span>Libya</span><span>Tunisia</span>
        <span>Afghanistan</span><span>Iraq</span><span>Turkey</span>
        <span>Sudan</span><span>Egypt</span><span>C. African Rep.</span>
        <span>Somalia</span><span>Rwanda</span><span>Somaliland</span>
      </div>
    </div>
  </div>
  <div class="footer-col inquiry-col">
    <div class="footer-head">Quick Inquiry</div>
    <div class="field">Your Name</div>
    <div class="field">Email Address</div>
    <div class="field">Phone</div>
    <div class="field msg">Message</div>
    <span class="submit">SUBMIT</span>
  </div>
  <div class="copyright">© 2015 Morvane Global Services. All rights reserved.</div>
</footer>

</div>
</body>
</html>
```